Financial Advisor Business Card

This business card is mainly a card for me personally (Marcus Obelwyn) providing services as a Financial Planner and Accountant. My title is: Brightway Mentor
Details provided about Harbourline Financial Advisors on the reverse side of the card is not dominant information, it is provided for ease of contact/communication purposes for prospective clients.
About me: I provide financial advice to my clients however due to regulatory issues in my industry I cannot use the title "Financial Advisor".
Target market is 25 y/o and onwards projecting a cutting edge, innovative and modern marketing influence.
Target Market(s)
25 years old and older
Industry/Entity Type
Financial
Contact Information for Business Card
Front side of business card
Name: Marcus Obelwyn
Position: Brightway Mentor
Accreditations:
Dip FS(FP)
B.Comm
Mobile: 0438 927 583
e-mail: mo@harbourlinefa.com.au
website: www.harbourlinefa.com.au
Reverse side of business card
Name: Marcus Obelwyn
Company: Harbourline Financial Advisors
Position: Senior Accountant
Address:
Level 6, Suite 4
47 Pelham Road
PO Box 718
KELSWORTH NSW 2291
Phone: (02) 49718352
Requirements
Must have
- - Cutting edge, innovative, fun but professional, modern marketing design and fonts
- Professional and legible
- Futuristic sharp lines, some with rounded edges
- Preferred Front Card colour scheme: Black background, Silver Text, White Text, Red & Silver lines
- Preferred Reverse Card colour scheme: White background, Silver Text, Black Text, Aqua & Silver lines
Nice to have
- Design a cutting edge logo of my intials as capital letters: MO
with a bigger D and smaller K - Preferred colour is Silver Text
Should not have
- Must not be:
- vintage/classic
- stereotypical accountant/tax agent/money style business card
- old style fonts e.g. times new roman

```html
<!DOCTYPE html>
<html lang="en">
<head>
<meta charset="utf-8">
<title>Marcus Obelwyn – Business Card</title>
<link href="https://fonts.googleapis.com/css2?family=Open+Sans:wght@300;400;600;700&display=swap" rel="stylesheet">
<style>
  :root {
    --backdrop: #e8e6e2;
    --card-white: #ffffff;
    --brand-blue: #1f6b8e;
    --brand-blue-deep: #17587a;
    --brand-blue-light: #2d86ab;
    --ink-grey: #555b60;
    --silver: #dfe3e6;
    --corner-black: #121416;
    --on-blue: #ffffff;
  }
  * { margin: 0; padding: 0; box-sizing: border-box; }
  html, body {
    width: 1200px; height: 1024px; overflow: hidden;
    background: var(--backdrop);
    font-family: "Open Sans", Arial, sans-serif;
  }
  .canvas { position: relative; width: 1200px; height: 1024px; }

  /* Front card */
  .card-front {
    position: absolute; left: 80px; top: 130px;
    width: 580px; height: 330px;
    background: var(--card-white);
    box-shadow: 0 8px 22px rgba(0,0,0,.18);
    overflow: hidden;
  }
  .front-band {
    position: absolute; left: 0; right: 0; bottom: 0; height: 46px;
    background: linear-gradient(90deg, var(--brand-blue-deep), var(--brand-blue-light));
  }
  .front-band-tip {
    position: absolute; right: 0; bottom: 0; width: 46px; height: 46px;
    background: var(--corner-black);
  }
  .front-wordmark {
    position: absolute; left: 40px; top: 120px;
    font-size: 54px; font-weight: 300; line-height: 1.08;
    color: var(--brand-blue);
  }
  .front-divider {
    position: absolute; left: 318px; top: 70px; width: 2px; height: 150px;
    background: linear-gradient(180deg, rgba(31,107,142,0), var(--brand-blue) 45%, rgba(31,107,142,0));
    transform: rotate(8deg);
  }
  .front-details {
    position: absolute; left: 350px; top: 48px;
    color: var(--ink-grey); font-size: 13px; line-height: 1.55;
  }
  .person-name { font-size: 17px; font-weight: 700; color: var(--brand-blue); line-height: 1.3; }
  .person-title, .person-credentials { font-size: 12.5px; }
  .contact-list { list-style: none; margin-top: 6px; }
  .contact-item { display: flex; align-items: center; gap: 7px; font-size: 13px; }
  .contact-icon { width: 11px; height: 11px; flex: none; }

  /* Back card */
  .card-back {
    position: absolute; left: 780px; top: 330px;
    width: 330px; height: 580px;
    background: linear-gradient(160deg, var(--brand-blue-light) 0%, var(--brand-blue) 55%, var(--brand-blue-deep) 100%);
    box-shadow: 0 8px 22px rgba(0,0,0,.22);
    overflow: hidden;
  }
  .back-wordmark {
    position: absolute; left: 86px; top: 200px;
    font-size: 40px; font-weight: 300; line-height: 1.1;
    color: var(--silver);
  }
  .back-website {
    position: absolute; left: 36px; top: 60px;
    transform-origin: left top; transform: rotate(90deg) translateY(-100%);
    font-size: 18px; color: var(--on-blue); white-space: nowrap; letter-spacing: .3px;
  }
  .company-details {
    position: absolute; left: 86px; top: 360px;
    color: var(--on-blue); font-size: 12px; line-height: 1.6;
  }
  .company-name { font-size: 13px; font-weight: 600; }
  .company-role { margin-bottom: 8px; }
</style>
</head>
<body>
<main class="canvas">

  <section class="card-front" aria-label="Card front">
    <p class="front-wordmark">Marcus<br>Obelwyn</p>
    <div class="front-divider"></div>
    <div class="front-details">
      <p class="person-name">Marcus Obelwyn</p>
      <p class="person-title">Brightway Mentor</p>
      <p class="person-credentials">Dip FS(FP) | B.Comm</p>
      <ul class="contact-list">
        <li class="contact-item">
          <svg class="contact-icon" viewBox="0 0 12 12"><rect x="2.5" y="0.5" width="7" height="11" rx="1.5" fill="none" stroke="#1f6b8e"/><line x1="5" y1="9.5" x2="7" y2="9.5" stroke="#1f6b8e"/></svg>
          0438 927 583
        </li>
        <li class="contact-item">
          <svg class="contact-icon" viewBox="0 0 12 12"><rect x="0.5" y="2" width="11" height="8" rx="1" fill="#1f6b8e"/><path d="M1 2.5 6 6.5 11 2.5" fill="none" stroke="#fff"/></svg>
          mo@harbourlinefa.com.au
        </li>
        <li class="contact-item">
          <svg class="contact-icon" viewBox="0 0 12 12"><circle cx="6" cy="6" r="5.5" fill="#1f6b8e"/><ellipse cx="6" cy="6" rx="2.3" ry="5.3" fill="none" stroke="#fff" stroke-width=".8"/><line x1=".5" y1="6" x2="11.5" y2="6" stroke="#fff" stroke-width=".8"/></svg>
          www.harbourlinefa.com.au
        </li>
      </ul>
    </div>
    <div class="front-band"></div>
    <div class="front-band-tip"></div>
  </section>

  <section class="card-back" aria-label="Card back">
    <p class="back-website">www.marcusobelwyn.com</p>
    <p class="back-wordmark">Marcus<br>Obelwyn</p>
    <div class="company-details">
      <p class="company-name">Harbourline Financial Advisors</p>
      <p class="company-role">Senior Accountant</p>
      <p>Level 6, Suite 4</p>
      <p>47 Pelham Road</p>
      <p>PO Box 718</p>
      <p>KELSWORTH NSW 2291</p>
      <p>(02) 49718352</p>
    </div>
  </section>

</main>
</body>
</html>
```